Pebblebrook Plots - Online-only garden installation company

Online-only garden installation company. Our demographic is middle aged / suburban women, and we anticipate Facebook driving traffic to this website, as well as referrals from garden centers. The website must be very simple in design and function.

All orders will be placed through the website, including size of garden (3 options), location in yard, payment, and scheduling of installation date.

The website should employ a 3 step process:

Step 1: Select garden size. Either an 4' X 4', 8' X 4', or 12' X 4'.

Step 2: Select a location. We would like to use google maps to look up a US address, then "drag and drop" one of the garden sizes from step 1 to the location the customer would like us to install the garden at their home.

Step 3: Pick an installation date and pay. Using an online calendar the customer will pick a date, and then pay for the installation via credit card.

The website will be linked to an email account, PebblebrookPlots@mailvale.com to inform us of orders placed.

Target Market(s)

Our demographic is middle aged / suburban women, and we anticipate Facebook driving traffic to this website, as well as referrals from garden centers.

Industry/Entity Type

Coding

Number of Pages Required

Requirements
Must have
• Scheduling and payment options.

```html
<!DOCTYPE html>
<html lang="en">
<head>
<meta charset="utf-8">
<title>Pebblebrook Plots – Garden Installation</title>
<link rel="stylesheet" href="https://fonts.googleapis.com/css2?family=Lato:wght@400;700;900&display=swap">
<style>
:root{
  --green:#3f7d3a;
  --green-dark:#356b31;
  --orange:#e05a2a;
  --ink:#1f1f1f;
  --muted:#666;
  --rule:#dcdcdc;
  --white:#fff;
}
*{box-sizing:border-box;margin:0;padding:0}
html,body{width:1200px;height:2844px;overflow:hidden}
body{font-family:'Lato',sans-serif;color:var(--ink);background:var(--white);position:relative}
.abs{position:absolute}

/* top bar */
.topbar{left:0;top:0;width:1200px;height:38px;background:var(--green);color:var(--white);font-size:12px}
.topbar .contact{left:160px;top:11px;display:flex;gap:28px;align-items:center}
.topbar .contact span{display:flex;align-items:center;gap:10px}
.socials{display:flex;gap:10px}
.socials i{display:block;width:20px;height:20px;border-radius:50%;background:var(--white)}
.topbar .socials{left:952px;top:9px}

/* header */
.brand{left:170px;top:88px;display:flex;align-items:center;gap:12px}
.brand .dot{width:40px;height:40px;border-radius:50%;background:var(--orange)}
.brand .name{font-weight:900;font-size:20px;color:var(--green);line-height:1.05;width:120px}
.search{left:641px;top:85px;width:259px;height:30px;border:1px solid #cfcfcf;display:flex}
.search span{flex:1;font-size:10px;color:#888;padding:9px 12px}
.search b,.cart b{width:30px;height:28px;background:var(--orange);display:flex;align-items:center;justify-content:center}
.cart{left:916px;top:85px;width:123px;height:30px;border:1px solid #cfcfcf;display:flex}
.cart span{flex:1;font-size:10px;color:#666;padding:9px 8px}
.nav{right:161px;top:143px;display:flex;gap:26px;font-size:14px;font-weight:700}

/* hero */
.hero{left:0;top:197px;width:1200px;height:425px;background:linear-gradient(120deg,#5d8f2f 0%,#a7c85a 35%,#e7efe2 50%,#7aa13f 70%,#2f4f2a 100%)}
.hero-dots{left:586px;top:578px;display:flex;gap:8px}
.hero-dots i{width:14px;height:14px;border-radius:50%;background:rgba(255,255,255,.6)}
.hero-dots i.on{background:var(--green)}

/* process */
.section-title{width:1200px;left:0;text-align:center;font-weight:900;font-size:30px}
.intro{left:340px;width:520px;text-align:center;font-size:11px;line-height:18px;color:var(--muted)}
.divider{left:570px;width:60px;height:2px;background:var(--green)}
.step{width:300px;text-align:center}
.step .icon{width:132px;height:132px;border-radius:50%;margin:0 auto;display:flex;align-items:center;justify-content:center}
.step h3{margin-top:38px;font-size:15px;font-weight:900}
.step p{margin-top:26px;font-size:13px;line-height:17px;color:var(--muted);padding:0 10px}
.bg-green{background:var(--green)}
.bg-orange{background:var(--orange)}
.step.active h3{color:var(--orange)}

/* address band */
.address-band{left:0;top:1174px;width:1200px;height:187px;background:linear-gradient(90deg,#3b2d22 0%,#5a4a36 40%,#2e3b22 75%,#4a5a33 100%)}
.address-band h2{left:159px;top:76px;color:var(--white);font-size:38px;font-weight:700;letter-spacing:1px}
.address-input{left:633px;top:72px;width:400px;height:56px;background:var(--white);display:flex;align-items:center;justify-content:space-between;padding:0 28px;font-size:13px;color:#999}

/* installation */
.install-photo{left:0;top:1361px;width:508px;height:596px;background:linear-gradient(160deg,#8fb8d8 0%,#b9a58a 30%,#5c8a3a 55%,#3a2d20 100%)}
.install-panel{left:508px;top:1361px;width:692px;height:596px;background:var(--orange);color:var(--white)}
.install-panel h2{position:absolute;left:0;top:64px;width:692px;text-align:center;font-size:30px;font-weight:700}
.install-panel .intro{left:146px;top:110px;width:400px;color:var(--white);font-size:11px;line-height:17px}
.install-panel .divider{left:316px;top:158px;background:var(--white)}
.field{left:63px;width:404px;height:52px;border:1px solid rgba(255,255,255,.8);display:flex;align-items:center;justify-content:space-between;padding:0 22px;font-size:11px}
.send{left:63px;top:482px;width:404px;height:63px;background:var(--green);display:flex;align-items:center;justify-content:center;font-size:15px;letter-spacing:.5px}

/* blog */
.blog-title{width:1200px;left:0;top:2025px;text-align:center;font-size:30px;font-weight:400}
.post{top:2086px;width:288px}
.post .thumb{height:216px}
.post h4{margin-top:26px;font-size:13px;font-weight:700}
.post p{margin-top:18px;font-size:10.5px;line-height:15px;color:var(--muted);text-align:justify}
.post a{display:block;margin-top:14px;font-size:10px;color:var(--orange);text-decoration:none}

/* footer */
.footer{left:0;top:2501px;width:1200px;height:343px;background:linear-gradient(180deg,#3a2a1f 0%,#2d231b 45%,#2d3f22 100%);color:var(--white)}
.footer .col{top:80px}
.footer h5{font-size:16px;font-weight:700;padding-bottom:12px;border-bottom:1px solid rgba(255,255,255,.25)}
.footer ul{list-style:none;margin-top:22px;font-size:11px}
.footer li{height:22px;display:flex;align-items:center;gap:14px}
.footer .socials{margin-top:20px}
.footer .note{margin-top:22px;font-size:11px;line-height:17px}
.mail{margin-top:22px;display:flex}
.mail span{width:212px;height:44px;border:1px solid rgba(255,255,255,.6);font-size:11px;padding:15px 16px;color:#ddd}
.mail b{width:53px;height:44px;background:var(--orange);display:flex;align-items:center;justify-content:center;margin-left:2px}
.footer .rule{left:159px;top:286px;width:880px;height:1px;background:rgba(255,255,255,.25)}
.footer .copy{left:159px;top:310px;font-size:11px}
.footer .code{left:1020px;top:310px;font-size:11px}
</style>
</head>
<body>

<div class="abs topbar">
  <div class="abs contact">
    <span><svg width="13" height="10" viewBox="0 0 13 10"><rect width="13" height="10" fill="#fff"/><path d="M0 0l6.5 5L13 0" stroke="#3f7d3a" fill="none"/></svg>hello@pebblebrookplots.com</span>
    <span><svg width="11" height="11" viewBox="0 0 24 24"><path fill="#fff" d="M6.6 10.8a15 15 0 006.6 6.6l2.2-2.2c.3-.3.7-.4 1-.2 1.1.4 2.3.6 3.6.6.6 0 1 .4 1 1V20c0 .6-.4 1-1 1A17 17 0 013 4c0-.6.4-1 1-1h3.5c.6 0 1 .4 1 1 0 1.3.2 2.5.6 3.6.1.3 0 .7-.2 1z"/></svg>555 214 0198</span>
  </div>
  <div class="abs socials"><i></i><i></i><i></i></div>
</div>

<div class="abs brand"><div class="dot"></div><div class="name">Pebblebrook Plots</div></div>
<div class="abs search"><span>Search</span><b><svg width="13" height="13" viewBox="0 0 14 14"><circle cx="6" cy="6" r="4.5" stroke="#fff" stroke-width="1.8" fill="none"/><path d="M9.5 9.5L13 13" stroke="#fff" stroke-width="1.8"/></svg></b></div>
<div class="abs cart"><span>Cart - $0.00</span><b><svg width="15" height="13" viewBox="0 0 16 14"><path d="M1 1h2.5l2 8h8l1.5-6H4.5" stroke="#fff" stroke-width="1.5" fill="none"/><circle cx="6.5" cy="12" r="1.2" fill="#fff"/><circle cx="12.5" cy="12" r="1.2" fill="#fff"/></svg></b></div>
<nav class="abs nav"><span>HOME</span><span>ABOUT US</span><span>PRODUCTS</span><span>SERVICES</span><span>GALLERY</span><span>CONTACT US</span></nav>

<div class="abs hero" role="img" aria-label="Photo of a child in a sunny vegetable garden holding up bunches of freshly pulled carrots"></div>
<div class="abs hero-dots"><i></i><i class="on"></i><i></i></div>

<h2 class="abs section-title" style="top:678px">OUR PROCESS</h2>
<p class="abs intro" style="top:716px">Plan, place and plant with us in three easy steps. Raised beds built to size, set in your yard and ready for your first seeds this season.</p>
<div class="abs divider" style="top:770px"></div>

<div class="abs step" style="left:163px;top:850px">
  <div class="icon bg-green"><svg width="64" height="64" viewBox="0 0 64 64" fill="#fff"><path d="M20 8l8 8 4-8 4 8 8-8v16c0 7-5 12-12 12s-12-5-12-12z"/><rect x="30" y="34" width="4" height="22"/><path d="M10 36c10 0 20 6 22 20C20 56 12 48 10 36zM54 36c-10 0-20 6-22 20 12 0 20-8 22-20z"/></svg></div>
  <h3>SELECT GARDEN SIZE</h3>
  <p>Three bed sizes to suit your yard, your plans and your time.</p>
</div>
<div class="abs step active" style="left:451px;top:850px">
  <div class="icon bg-orange"><svg width="54" height="66" viewBox="0 0 54 66"><path d="M27 2C14 2 4 12 4 25c0 17 23 39 23 39s23-22 23-39C50 12 40 2 27 2z" fill="#fff"/><circle cx="27" cy="24" r="9" fill="#e05a2a"/></svg></div>
  <h3>SELECT A LOCATION</h3>
  <p>Find your home on the map and drop the bed where it fits.</p>
</div>
<div class="abs step" style="left:754px;top:850px">
  <div class="icon bg-green"><svg width="70" height="70" viewBox="0 0 70 70"><rect x="6" y="10" width="48" height="44" rx="4" fill="none" stroke="#fff" stroke-width="4"/><rect x="6" y="10" width="48" height="10" fill="#fff"/><rect x="15" y="4" width="4" height="12" fill="#fff"/><rect x="41" y="4" width="4" height="12" fill="#fff"/><g fill="#fff"><rect x="13" y="26" width="6" height="6"/><rect x="23" y="26" width="6" height="6"/><rect x="33" y="26" width="6" height="6"/><rect x="13" y="36" width="6" height="6"/><rect x="23" y="36" width="6" height="6"/></g><circle cx="50" cy="50" r="15" fill="#e05a2a" stroke="#3f7d3a" stroke-width="3"/><text x="50" y="57" text-anchor="middle" fill="#fff" font-family="Lato,sans-serif" font-weight="900" font-size="19">$</text></svg></div>
  <h3>INSTALLATION DATE &amp; PAY</h3>
  <p>Pick a day on the calendar and pay safely by card online.</p>
</div>

<section class="abs address-band" role="img" aria-label="Photo of hands planting seedlings in dark garden soil">
  <h2 class="abs">SELECT &nbsp;ADDRESS</h2>
  <div class="abs address-input"><span>Search Your Address</span><svg width="16" height="14" viewBox="0 0 16 14"><path d="M0 6L16 0 11 14 8 8z" fill="#e05a2a"/></svg></div>
</section>

<div class="abs install-photo" role="img" aria-label="Photo of a gardener kneeling in a backyard vegetable bed in front of suburban houses"></div>
<section class="abs install-panel">
  <h2>INSTALLATION NOW</h2>
  <p class="abs intro">Tell us the size, the spot in your yard and the day that suits you. We build it, fill it and leave it ready.</p>
  <div class="abs divider"></div>
  <div class="abs field" style="top:201px"><span>Size of Garden</span><svg width="16" height="16" viewBox="0 0 16 16"><circle cx="8" cy="8" r="8" fill="#fff"/><path d="M8 4v7M5 8l3 3 3-3" stroke="#e05a2a" stroke-width="1.6" fill="none"/></svg></div>
  <div class="abs field" style="top:270px"><span>Location in Yard</span><svg width="12" height="16" viewBox="0 0 12 16"><path d="M6 0a6 6 0 00-6 6c0 4 6 10 6 10s6-6 6-10a6 6 0 00-6-6z" fill="#fff"/><circle cx="6" cy="6" r="2.2" fill="#e05a2a"/></svg></div>
  <div class="abs field" style="top:340px"><span>Payment</span><svg width="18" height="13" viewBox="0 0 18 13"><rect x="1" y="1" width="16" height="11" rx="1.5" fill="none" stroke="#fff" stroke-width="1.6"/><rect x="1" y="4" width="16" height="2.5" fill="#fff"/></svg></div>
  <div class="abs field" style="top:406px"><span>Installation Date</span><svg width="15" height="15" viewBox="0 0 15 15"><rect x="1" y="2" width="13" height="12" rx="1" fill="none" stroke="#fff" stroke-width="1.5"/><rect x="1" y="2" width="13" height="3" fill="#fff"/><path d="M5 9l2 2 3-4" stroke="#fff" stroke-width="1.4" fill="none"/></svg></div>
  <div class="abs send">SEND</div>
</section>

<h2 class="abs blog-title">LATEST BLOG</h2>
<article class="abs post" style="left:161px">
  <div class="thumb" role="img" aria-label="Photo of potted flowers, a watering can and garden tools on a wooden table" style="background:linear-gradient(135deg,#5c7fa0,#c86ca6 45%,#e6c640 70%,#4f7a33)"></div>
  <h4>Li Europan lingues es membres del</h4>
  <p>Fresh beds need little care in the first weeks. Water deeply in the morning, keep weeds down early and add mulch once seedlings are up. Small habits now mean a fuller harvest, and a few minutes each evening keeps pests away from tender leaves.</p>
  <a>Read More &gt;</a>
</article>
<article class="abs post" style="left:457px">
  <div class="thumb" role="img" aria-label="Close photo of freshly dug carrots with green tops in soil" style="background:linear-gradient(135deg,#3a2a1e,#c5622a 40%,#d9894a 60%,#4d7a2e)"></div>
  <h4>Li Europan lingues es membres del</h4>
  <p>Fresh beds need little care in the first weeks. Water deeply in the morning, keep weeds down early and add mulch once seedlings are up. Small habits now mean a fuller harvest, and a few minutes each evening keeps pests away from tender leaves.</p>
  <a>Read More &gt;</a>
</article>
<article class="abs post" style="left:751px">
  <div class="thumb" role="img" aria-label="Photo of gloved hands potting pink flowers in a sunny garden" style="background:linear-gradient(135deg,#f1e38a,#7fb04a 40%,#b66aa8 65%,#8a5a3a)"></div>
  <h4>Li Europan lingues es membres del</h4>
  <p>Fresh beds need little care in the first weeks. Water deeply in the morning, keep weeds down early and add mulch once seedlings are up. Small habits now mean a fuller harvest, and a few minutes each evening keeps pests away from tender leaves.</p>
  <a>Read More &gt;</a>
</article>

<footer class="abs footer" role="img" aria-label="Photo of potted herbs and garden forks on a wooden fence and grass, darkened behind the footer">
  <div class="abs col" style="left:159px;width:258px">
    <h5>Get In Touch</h5>
    <ul>
      <li><svg width="10" height="13" viewBox="0 0 12 16"><path d="M6 0a6 6 0 00-6 6c0 4 6 10 6 10s6-6 6-10a6 6 0 00-6-6z" fill="#fff"/></svg>48 Alder Lane, Fairview Ohio 43001 US.</li>
      <li><svg width="11" height="11" viewBox="0 0 24 24"><path fill="#fff" d="M6.6 10.8a15 15 0 006.6 6.6l2.2-2.2c.3-.3.7-.4 1-.2 1.1.4 2.3.6 3.6.6.6 0 1 .4 1 1V20c0 .6-.4 1-1 1A17 17 0 013 4c0-.6.4-1 1-1h3.5c.6 0 1 .4 1 1 0 1.3.2 2.5.6 3.6.1.3 0 .7-.2 1z"/></svg>555 214 0173.</li>
      <li><svg width="12" height="9" viewBox="0 0 13 10"><rect width="13" height="10" fill="#fff"/><path d="M0 0l6.5 5L13 0" stroke="#333" fill="none"/></svg>PebblebrookPlots@mailvale.com</li>
    </ul>
    <div class="socials"><i></i><i></i><i></i></div>
  </div>
  <div class="abs col" style="left:461px;width:272px">
    <h5>Quick Links</h5>
    <ul><li>&gt; Home</li><li>&gt; About Us</li><li>&gt; Services</li><li>&gt; Products</li><li>&gt; Contact Us</li></ul>
  </div>
  <div class="abs col" style="left:764px;width:275px">
    <h5>Mailing List</h5>
    <p class="note">Enter your mail address for our mailing list to keep yourself update.</p>
    <div class="mail"><span>Email</span><b><svg width="20" height="18" viewBox="0 0 16 14"><path d="M0 6L16 0 11 14 8 8z" fill="#fff"/></svg></b></div>
  </div>
  <div class="abs rule"></div>
  <p class="abs copy">Copyright © Pebblebrook Plots 2017. All rights reserved.</p>
  <p class="abs code">c24</p>
</footer>

</body>
</html>
```